Economics of an Assumption vs Obtaining a New Loan at Current Market Rate

I need to marketing flyer that has fields that calculate mortgage payments amongst other calculations. I have a rough draft that I will attach.

The idea is to provide a tool for a real estate agent to use to illustrate to a potential buyer what a payment would be if they assumed the existing loan on the house or took out a new loan at current market.

The flyer needs to be able to allow an agent to drop in their logo, photo, and contact along with the loan officers photo and contact info.

You can google open house flyer to see examples of what the overall artwork and presentation can look like.

Target Market(s)

Home Buyers

Industry/Entity Type

Real Estate

Colors
F0912C
F2A743
F7CA91
FBE8D2
FDF5EE
EE7325
F08F49
F5BC92
FAE3D3
FDF4ED

Requirements
Must have
• A way to calculate mortgage payment
Nice to have
• Photo and logo drop ins

```html
<!DOCTYPE html>
<html lang="en">
<head>
<meta charset="utf-8">
<title>Orvane – Assumption vs New Loan Flyer</title>
<link rel="stylesheet" href="https://fonts.googleapis.com/css2?family=Source+Sans+3:wght@400;500;600;700&family=Open+Sans:wght@700&family=Great+Vibes&display=swap">
<style>
  :root{
    --navy:#111b2b;
    --sky:#3cbfef;
    --orange:#ee7325;
    --ink:#1b1f27;
    --white:#ffffff;
  }
  *{box-sizing:border-box;margin:0;padding:0}
  html,body{width:848px;height:1200px;overflow:hidden;background:var(--white)}
  .flyer{position:relative;width:848px;height:1200px;overflow:hidden;background:var(--white);
    font-family:"Source Sans 3",Arial,sans-serif;color:var(--ink)}
  .abs{position:absolute}

  .brand{left:58px;top:110px;display:flex;align-items:center;gap:12px}
  .brand-mark{width:26px;height:26px;background:var(--orange)}
  .brand-name{font-size:64px;font-weight:400;color:var(--orange);letter-spacing:1px;line-height:1}

  .price-band{left:0;top:276px;width:560px;height:115px;background:var(--navy)}
  .hero{left:0;top:0;width:848px;height:440px}
  .price-title{left:24px;top:284px;font-size:31px;font-weight:700;color:var(--sky);letter-spacing:.3px}
  .price-field{left:22px;top:331px;width:373px;height:42px;border:2px solid var(--white);border-radius:5px}

  .section-head{top:420px;height:45px;background:var(--sky);color:var(--white);
    font-family:"Open Sans",Arial,sans-serif;font-weight:700;display:flex;align-items:center;white-space:nowrap}
  .section-head.current{left:22px;width:345px;font-size:21px;letter-spacing:1.6px;padding-left:6px}
  .section-head.new{left:400px;width:422px;font-size:21px;letter-spacing:1.3px;padding-left:4px}

  .row{position:absolute;font-size:21px;font-weight:500;line-height:1;white-space:nowrap}
  .field{position:absolute;height:23px;border:1.5px solid var(--ink)}

  .diff-title{left:24px;top:745px;font-size:31px;font-weight:700;color:var(--sky)}
  .diff-field{left:22px;top:787px;width:373px;height:42px;border:1.5px solid var(--ink);border-radius:5px}

  .cert-band{left:0;top:848px;width:848px;height:105px;background:var(--navy);text-align:center;color:var(--white)}
  .cert-kicker{font-family:"Open Sans",Arial,sans-serif;font-weight:700;font-size:20px;letter-spacing:1.5px;margin-top:10px}
  .cert-line{font-family:"Great Vibes",cursive;font-size:50px;line-height:1;margin-top:0;letter-spacing:1px;white-space:nowrap}

  .info-head{left:22px;top:966px;width:238px;height:48px;
    background:linear-gradient(90deg,var(--sky) 55%,rgba(60,191,239,0) 100%)}
  .info-title{left:38px;top:966px;font-size:40px;font-weight:700;color:var(--navy);line-height:48px;white-space:nowrap}
  .contact{position:absolute;left:44px;display:flex;align-items:center;font-size:21px;color:var(--ink)}
  .contact svg{width:24px;height:24px;margin-right:28px}
  .contact b{font-weight:700}

  .phone-bar{left:0;top:1120px;width:848px;height:80px}
  .phone-number{left:92px;top:1145px;font-size:30px;font-weight:700;color:var(--white);letter-spacing:.8px}

  .thumb{position:absolute;top:987px;width:144px;height:179px;border:4px solid var(--navy);border-radius:13px;overflow:hidden}
  .thumb.photo{left:465px;background:linear-gradient(180deg,#8a9cc4 0%,#b7b4c1 35%,#a88462 60%,#8d6d50 85%,#b9b2a6 100%)}
  .thumb.logo{left:629px;display:flex;align-items:center;justify-content:center;gap:6px;background:var(--white)}
  .thumb.logo .brand-mark{width:10px;height:10px}
  .thumb.logo .brand-name{font-size:28px}
</style>
</head>
<body>
<div class="flyer">

  <div class="abs price-band"></div>
  <svg class="abs hero" viewBox="0 0 848 440">
    <defs>
      <linearGradient id="houseTones" x1="0" y1="0" x2="0" y2="1">
        <stop offset="0" stop-color="#7f93c0"/>
        <stop offset=".3" stop-color="#b4b1c0"/>
        <stop offset=".55" stop-color="#ab8763"/>
        <stop offset=".82" stop-color="#8e6e51"/>
        <stop offset="1" stop-color="#b8b0a4"/>
      </linearGradient>
    </defs>
    <circle cx="690" cy="112" r="304" fill="var(--sky)"/>
    <circle cx="676" cy="112" r="304" fill="var(--navy)"/>
    <circle cx="692" cy="108" r="292" fill="url(#houseTones)" role="img" aria-label="Exterior photo of the featured house"/>
  </svg>

  <div class="abs brand">
    <span class="brand-mark"></span>
    <span class="brand-name">Orvane</span>
  </div>

  <div class="abs price-title">PURCHASE PRICE :</div>
  <div class="abs price-field"></div>

  <div class="abs section-head current">CURRENT MORTGAGE :</div>
  <div class="abs section-head new">New Mortgage 10% Down Payment</div>

  <div class="row" style="left:28px;top:484px">Loan ammount</div><div class="row" style="left:229px;top:484px">:</div><div class="field" style="left:248px;top:482px;width:117px"></div>
  <div class="row" style="left:28px;top:518px">Interest rate</div><div class="row" style="left:229px;top:518px">:</div><div class="field" style="left:248px;top:516px;width:117px"></div>
  <div class="row" style="left:28px;top:552px">Principal 3 interest</div><div class="row" style="left:229px;top:552px">:</div><div class="field" style="left:248px;top:550px;width:117px"></div>
  <div class="row" style="left:28px;top:586px">Mortgage Insurance :</div><div class="field" style="left:248px;top:584px;width:117px"></div>
  <div class="row" style="left:28px;top:620px">Total</div><div class="row" style="left:229px;top:620px">:</div><div class="field" style="left:248px;top:618px;width:117px"></div>
  <div class="row" style="left:28px;top:654px">Years</div><div class="field" style="left:90px;top:652px;width:58px"></div>
  <div class="row" style="left:157px;top:654px">Months</div><div class="field" style="left:248px;top:652px;width:58px"></div>
  <div class="row" style="left:28px;top:688px">Delta</div><div class="field" style="left:90px;top:686px;width:272px"></div>

  <div class="row" style="left:403px;top:484px">Loan ammount</div><div class="row" style="left:604px;top:484px">:</div><div class="field" style="left:622px;top:482px;width:200px"></div>
  <div class="row" style="left:403px;top:518px">Interest rate</div><div class="row" style="left:604px;top:518px">:</div><div class="field" style="left:622px;top:516px;width:200px"></div>
  <div class="row" style="left:403px;top:552px">Principal 3 interest</div><div class="row" style="left:604px;top:552px">:</div><div class="field" style="left:622px;top:550px;width:200px"></div>
  <div class="row" style="left:403px;top:586px">Mortgage Insurance :</div><div class="field" style="left:622px;top:584px;width:200px"></div>
  <div class="row" style="left:403px;top:620px">Total</div><div class="row" style="left:604px;top:620px">:</div><div class="field" style="left:622px;top:618px;width:200px"></div>
  <div class="row" style="left:403px;top:654px">Term</div><div class="field" style="left:465px;top:652px;width:58px"></div>
  <div class="row" style="left:532px;top:654px">Years</div>
  <div class="row" style="left:403px;top:688px">Down payment amount</div><div class="field" style="left:649px;top:686px;width:59px"></div>

  <div class="abs diff-title">PAYMENT DIFFERENCE :</div>
  <div class="abs diff-field"></div>

  <div class="abs cert-band">
    <div class="cert-kicker">THIS PROPERTY IS :</div>
    <div class="cert-line">“Smart Rate Assumption Approved”</div>
  </div>

  <div class="abs info-head"></div>
  <div class="abs info-title">More Information :</div>

  <div class="contact" style="top:1028px">
    <svg viewBox="0 0 24 24"><path fill="var(--navy)" d="M6.6 2.5l3 3.2-1.8 2.6c1 2.3 3.3 4.7 5.8 5.9l2.6-1.8 3.3 3-1.6 3.4C10.6 18.6 5.4 13.4 3.2 4.2z"/></svg>
    <span>MOBILE : <b>0123456789</b></span>
  </div>
  <div class="contact" style="top:1060px">
    <svg viewBox="0 0 24 24"><circle cx="12" cy="12" r="10" fill="var(--navy)"/><path d="M2 12h20M12 2v20M4.5 7h15M4.5 17h15M12 2c-4 4-4 16 0 20M12 2c4 4 4 16 0 20" stroke="#fff" stroke-width="1.2" fill="none"/></svg>
    <span>www.<b>yourwebsite</b>.com</span>
  </div>
  <div class="contact" style="top:1092px">
    <svg viewBox="0 0 24 24"><path fill="var(--navy)" d="M2 9l10-7 10 7v12H2z"/><path d="M2 9l10 7 10-7M2 21l8-6M22 21l-8-6" stroke="#fff" stroke-width="1.2" fill="none"/></svg>
    <span>youremailhere@postvale.com</span>
  </div>

  <svg class="abs phone-bar" viewBox="0 0 848 80">
    <rect x="290" y="69" width="558" height="11" fill="var(--sky)"/>
    <path d="M0 3 H240 C280 3 290 30 308 80 H0 Z" fill="var(--navy)"/>
    <circle cx="46" cy="44" r="18" fill="none" stroke="#fff" stroke-width="2.5"/>
    <path transform="translate(35 33) scale(0.9)" fill="#fff" d="M6.6 2.5l3 3.2-1.8 2.6c1 2.3 3.3 4.7 5.8 5.9l2.6-1.8 3.3 3-1.6 3.4C10.6 18.6 5.4 13.4 3.2 4.2z"/>
  </svg>
  <div class="abs phone-number">1234567890</div>

  <div class="thumb photo" role="img" aria-label="Agent or property photo"></div>
  <div class="thumb logo">
    <span class="brand-mark"></span>
    <span class="brand-name">Orvane</span>
  </div>

</div>
</body>
</html>
```